Desktop and Mobile Home Page Redesign

Please tailor the attached wireframe i made with your own design.
The key is to have the social icons being prominent, then have effectively 3 rows of mis-leveled posts to track the eye down the page.
At the bottom, I would like for you to design the same post types that dailyvortle.com.au have (attached) - I did not have time to add it into the wire frame.
Please design your own elements rather than taking from other sites direct.
Check out pelinora.com.au
We need a home page design for mobile and desktop (adaptive)
Must have features (desktop)
- Call to action buttons (large and attractive eg "Get More")
- The new redesign must be familiar to the old
- The design must have elements that prompt the user to scroll down e.g the video tab on the left of http://quorbit.com.au/ which forces the eye down
- Must have image galleries incorporated on the home page
-Must have room for 2 350x250 banners, 2 160x600 banners and 2 728x90 banners
- Must have originally formatted content in the middle of the page that would encourage navigation DEEP into the site (e.g think about how to format posts, polls, sliders, lists, galleries, videos, categories and menus, star rating)
- Must keep footer
- Must be adaptive
- Must have large and prominent share icons for each article and piece of content
- Must have a way to easily view comments
Must have features (mobile)
- Adaptive to zentrix and vaLphone
- Adaptive to both horizontal and vertical
- Easy tapping ability (finger size)
-Must have room for mobile banners
Updates
Target Market(s)
Females
Industry/Entity Type
Tailor
Requirements
Must have
- Check out pelinora.com.au
- Hero post
- Must keep footer
- Must be adaptive

```html
<!DOCTYPE html>
<html lang="en">
<head>
<meta charset="utf-8">
<title>Pelinora — Home</title>
<link href="https://fonts.googleapis.com/css2?family=Open+Sans:wght@400;600;700;800&family=Oswald:wght@500&display=swap" rel="stylesheet">
<style>
:root{
  --blue:#1e88d6;--navy:#1d3d6b;--green:#7cb82f;--red:#e4322b;--purple:#8a3ea0;
  --yellow:#f2c11b;--pink:#e5458f;--orange:#f08a24;--ink:#222;--muted:#666;
  --line:#dcdcdc;--panel:#f3f3f3;--black:#0d0d0d;
}
*{box-sizing:border-box;margin:0;padding:0}
html,body{width:1200px;height:2608px;overflow:hidden;background:#fff}
body{position:relative;font-family:"Open Sans",Arial,sans-serif;color:var(--ink);font-size:12px;line-height:1.4}
a{color:inherit;text-decoration:none}
.abs{position:absolute}
.photo{border-radius:2px}

/* header */
.brand{left:150px;top:12px;width:320px}
.brand-name{display:flex;align-items:center;gap:10px;font-size:44px;font-weight:800;color:var(--ink);line-height:1}
.brand-name i{width:16px;height:16px;background:var(--pink);display:block}
.brand-tag{font-size:13px;color:var(--muted);margin:6px 0 0 26px}
.top-banner{left:480px;top:8px;width:530px;height:72px;display:flex;border:1px solid var(--line)}
.top-banner .photo{width:170px;height:100%;background:linear-gradient(135deg,#f6f6f6,#e94b3c);border-radius:0}
.top-banner .ad-copy{flex:1;background:linear-gradient(90deg,#2c8fe0,#1b5fb0);color:#fff;font-size:24px;font-weight:700;display:flex;align-items:center;padding-left:24px}
.search{left:1020px;top:12px;width:140px;height:24px;border:1px solid var(--line);display:flex}
.search span{flex:1;font-size:10px;color:#999;padding:4px 6px}
.search b{width:24px;background:var(--blue)}

.main-nav{left:150px;top:88px;width:1010px;height:32px;display:flex}
.main-nav a{color:#fff;font-weight:700;font-size:13px;display:flex;align-items:center;justify-content:center;text-transform:uppercase}
.sub-nav{left:150px;top:122px;width:1010px;height:30px;border-bottom:1px solid var(--line);display:flex;align-items:center;font-size:10px;color:var(--muted);gap:10px;text-transform:uppercase}
.sub-nav .dots{margin-left:auto;display:flex;gap:5px}
.dot{width:14px;height:14px;border-radius:50%;display:inline-block}

/* hero */
.hero{left:150px;top:166px;width:602px;height:300px;display:grid;grid-template-columns:340px 258px;grid-template-rows:148px 148px;gap:4px}
.hero-tile{position:relative;overflow:hidden}
.hero-cap{position:absolute;left:0;right:0;bottom:0;padding:8px 10px;background:linear-gradient(transparent,rgba(0,0,0,.75));color:#fff}
.hero-cap h2{font-size:17px;font-weight:700;line-height:1.2}
.hero-cap p{font-size:9px;opacity:.85}
.btn-read{display:inline-block;background:var(--red);color:#fff;font-size:9px;font-weight:700;padding:2px 7px;border-radius:2px;margin-top:3px}

/* category column */
.cat-col{left:150px;top:490px;width:190px}
.cat{height:200px;margin-bottom:10px}
.cat-tab{display:inline-block;color:#fff;font-weight:700;font-size:12px;padding:3px 12px;margin-bottom:4px}
.cat .photo{height:100px}
.cat h4{font-size:12px;font-weight:700;margin-top:6px;line-height:1.3}
.cat p{font-size:10px;color:var(--muted)}

/* feed */
.talk{left:352px;top:476px;background:var(--yellow);color:var(--ink);font-weight:800;font-size:14px;padding:4px 14px}
.feed{left:352px;top:510px;width:400px}
.post{height:110px;margin-bottom:10px;display:flex;gap:8px}
.post.flip{flex-direction:row-reverse}
.post-photo{width:272px;height:110px;position:relative}
.post-cap{position:absolute;left:0;right:0;bottom:0;padding:6px 10px;background:linear-gradient(transparent,rgba(10,25,60,.85));color:#fff}
.post-cap h3{font-size:18px;font-weight:700;line-height:1.15}
.post-cap p{font-size:9px;opacity:.9}
.post-side{flex:1;display:flex;flex-direction:column;gap:6px}
.post-side .photo{flex:1}
.share{display:flex;gap:4px}
.share span{flex:1;font-size:9px;font-weight:700;color:#fff;text-align:center;padding:3px 0;border-radius:2px}

/* sidebar */
.side{left:764px;top:166px;width:396px}
.weather{height:96px;background:linear-gradient(180deg,#17355f,#0b1f3c);color:#fff;padding:10px 12px;display:flex;gap:10px}
.weather .photo{width:110px}
.weather h5{font-size:13px}
.weather p{font-size:10px;opacity:.8}
.weather .temp{font-size:28px;font-weight:800}
.ad-mrec{height:248px;margin-top:10px;background:linear-gradient(160deg,#e9f4da,#6aa63a);position:relative}
.ad-mrec span{position:absolute;left:24px;top:20px;font-size:40px;font-weight:800;color:#fff}
.video{height:230px;margin-top:10px;background:var(--navy);padding:8px;color:#fff}
.video h5{font-size:12px;font-weight:800;text-transform:uppercase;line-height:1.25}
.video .photo{height:148px;margin:6px 0;position:relative}
.play{position:absolute;left:50%;top:50%;width:44px;height:44px;margin:-22px 0 0 -22px}
.video .btns{display:flex;justify-content:space-between}
.btn{display:inline-block;color:#fff;font-weight:700;font-size:11px;padding:5px 14px;border-radius:3px;text-transform:uppercase}
.signup{height:100px;margin-top:10px;padding:6px 8px;border:1px solid var(--line)}
.signup h5{color:var(--red);font-size:14px;font-weight:700}
.signup .row{display:flex;gap:6px;margin-top:6px}
.signup .field{flex:1;border:1px solid var(--line);font-size:10px;color:#999;padding:5px 6px}
.follow{display:flex;align-items:center;gap:6px;margin-top:8px;font-weight:800;font-size:11px}
.fb{height:320px;margin-top:10px;border:1px solid var(--line)}
.fb-head{background:#e9edf4;padding:6px 8px;font-weight:700;font-size:12px;color:var(--navy)}
.fb-page{display:flex;gap:8px;padding:8px}
.fb-page .photo{width:48px;height:48px}
.fb-page p{font-size:10px;color:var(--muted)}
.fb-grid{display:grid;grid-template-columns:repeat(6,1fr);gap:6px;padding:4px 8px}
.fb-grid div{height:48px;background:linear-gradient(135deg,#d9c6b6,#8e7566)}
.fb-grid small{display:block;font-size:8px;color:var(--muted);text-align:center;margin-top:50px}
.fb-foot{font-size:9px;color:#999;padding:18px 8px 0}
.galleries{height:170px;margin-top:12px;border:1px solid var(--line)}
.galleries h5{background:var(--blue);color:#fff;font-size:13px;font-weight:800;padding:5px 10px;text-transform:uppercase}
.gal-grid{display:grid;grid-template-columns:repeat(3,1fr);gap:8px;padding:8px}
.gal-grid .photo{height:46px}
.gal-grid p{font-size:9px;color:var(--muted);line-height:1.2;margin-top:2px}
.zodiac{height:220px;margin-top:12px;background:radial-gradient(circle at 50% 50%,#5a4aa8 0,#2a2a78 45%,#10154a 70%)}

/* lower sections */
.band{left:150px;width:1010px}
.band-tab{display:inline-block;color:#fff;font-weight:700;font-size:13px;padding:3px 14px}
.band-body{display:flex;gap:30px;margin-top:6px;border-top:2px solid var(--line);padding-top:8px}
.mosaic{width:560px;display:grid;gap:4px}
.copy{flex:1}
.copy p{font-size:12px;color:#333;line-height:1.45}
.copy .share{width:180px;margin:6px 0 14px}

/* footer */
.footer{left:150px;top:2250px;width:1010px;height:350px;background:var(--black);color:#bbb;padding:16px 22px}
.footer .brand-name{font-size:34px;color:#fff}
.footer .brand-tag{color:#999}
.foot-cols{display:flex;gap:26px;margin-top:22px}
.foot-cols ul{list-style:none;width:148px}
.foot-cols li{font-size:10px;line-height:1.75}
.foot-cols li::before{content:"› ";color:var(--pink)}
.stay{margin-left:auto;width:150px}
.stay h6{font-size:11px;color:#fff;margin-bottom:8px}
.footer .legal{position:absolute;left:22px;bottom:12px;font-size:10px;color:#888}
.footer .badge{position:absolute;right:22px;bottom:10px;width:90px;height:26px;background:#3a3a3a}
</style>
</head>
<body>

<header>
  <div class="brand abs"><div class="brand-name"><i></i>Pelinora</div><div class="brand-tag">what everyone is talking about</div></div>
  <div class="top-banner abs"><div class="photo" role="img" aria-label="Brightmart catalogue advertisement product photo"></div><div class="ad-copy">View our catalogue now</div></div>
  <div class="search abs"><span>www.pelinora.com.au</span><b></b></div>

  <nav class="main-nav abs">
    <a style="width:64px;background:var(--blue)">Home</a>
    <a style="width:64px;background:var(--navy)">News</a>
    <a style="width:70px;background:var(--green)">Style</a>
    <a style="width:76px;background:var(--red)">Social</a>
    <a style="width:246px;background:var(--green)">Relationships</a>
    <a style="width:250px;background:var(--purple)">Entertainment</a>
    <a style="width:240px;background:var(--yellow)">Parenting</a>
  </nav>
  <div class="sub-nav abs">
    <span>Product Reviews</span>|<span>Travel</span>|<span>Lifestyle</span>|<span>Food</span>|<span>Videos</span>|<span>Pelinora Chat</span>|<span>About</span>|<span>Advertise</span>|<span>Contact</span>
    <span class="dots"><i class="dot" style="background:#3b5b9a"></i><i class="dot" style="background:#29a9e1"></i><i class="dot" style="background:#d9342b"></i><i class="dot" style="background:#f08a24"></i></span>
  </div>
</header>

<section class="hero abs">
  <div class="hero-tile photo" role="img" aria-label="Family group photo for lead story" style="background:linear-gradient(135deg,#d8b89a,#6d4c3a)"><div class="hero-cap"><h2>Everything, Line Dropping 100!</h2><p>A short lead line to open the story</p><a class="btn-read">Read More</a></div></div>
  <div class="hero-tile photo" role="img" aria-label="Woman portrait for second story" style="background:linear-gradient(135deg,#c4a48a,#3e2a24)"><div class="hero-cap"><h2>Clandestine Title</h2><p>Quick teaser about this story</p><a class="btn-read">Read More</a></div></div>
  <div class="hero-tile photo" role="img" aria-label="Couple photo for third story" style="background:linear-gradient(135deg,#b9a58f,#54463c)"><div class="hero-cap"><h2>Controversial Title</h2><p>Quick teaser about this story</p><a class="btn-read">Read More</a></div></div>
  <div class="hero-tile photo" role="img" aria-label="Portrait photo for fourth story" style="background:linear-gradient(135deg,#e0c7b0,#7b5a48)"><div class="hero-cap"><h2>Provocative Topic</h2><p>Quick teaser about this story</p><a class="btn-read">Read More</a></div></div>
</section>

<aside class="cat-col abs">
  <div class="cat"><span class="cat-tab" style="background:var(--blue)">Social</span><div class="photo" role="img" aria-label="Man at a microphone" style="background:linear-gradient(135deg,#b8c6d6,#4a5e78)"></div><h4>Why this man needs to dye his hair</h4><p>A short line of text to tease this story.</p></div>
  <div class="cat"><span class="cat-tab" style="background:var(--pink)">Parenting</span><div class="photo" role="img" aria-label="Mother with child" style="background:linear-gradient(135deg,#e7d2c1,#9b7a66)"></div><h4>New contraception is failing</h4><p>A short line of text to tease this story.</p></div>
  <div class="cat"><span class="cat-tab" style="background:var(--purple)">Body Image</span><div class="photo" role="img" aria-label="Woman outdoors" style="background:linear-gradient(135deg,#c9d9b7,#6f8a5a)"></div><h4>Pretending to be injured for gifts</h4><p>A short line of text to tease this story.</p></div>
  <div class="cat"><span class="cat-tab" style="background:var(--red)">News</span><div class="photo" role="img" aria-label="Two women in a news photo" style="background:linear-gradient(135deg,#d6c0aa,#5d4738)"></div><h4>Spot the difference</h4><p>A short line of text to tease this story.</p></div>
  <div class="cat"><span class="cat-tab" style="background:var(--orange)">Beauty</span><div class="photo" role="img" aria-label="Beauty portrait" style="background:linear-gradient(135deg,#e8c49a,#8a5a34)"></div><h4>Hair looks for the new season</h4><p>A short line of text to tease this story.</p></div>
</aside>

<div class="talk abs">Today we're Talking About</div>
<main class="feed abs">
  <article class="post"><div class="post-photo photo" role="img" aria-label="Story photo" style="background:linear-gradient(135deg,#c8b09a,#4c3a30)"><div class="post-cap"><h3>Outrageous Info</h3><p>Short teaser text sitting under the headline</p><a class="btn-read">Read More</a></div></div><div class="post-side"><div class="photo" role="img" aria-label="Related photo" style="background:linear-gradient(135deg,#d7c3b3,#7d6252)"></div><div class="share"><span style="background:#3b5b9a">Share</span><span style="background:#29a9e1">Post</span></div></div></article>
  <article class="post flip"><div class="post-photo photo" role="img" aria-label="Story photo" style="background:linear-gradient(135deg,#b7c4d2,#39475a)"><div class="post-cap"><h3>Hilarious Commentary</h3><p>Short teaser text sitting under the headline</p><a class="btn-read">Read More</a></div></div><div class="post-side"><div class="photo" role="img" aria-label="Related photo" style="background:linear-gradient(135deg,#e1cdb8,#94725b)"></div><div class="share"><span style="background:#3b5b9a">Share</span><span style="background:#29a9e1">Post</span></div></div></article>
  <article class="post"><div class="post-photo photo" role="img" aria-label="Story photo" style="background:linear-gradient(135deg,#d9bfa6,#6a4a36)"><div class="post-cap"><h3>Outrageous Info</h3><p>Short teaser text sitting under the headline</p><a class="btn-read">Read More</a></div></div><div class="post-side"><div class="photo" role="img" aria-label="Related photo" style="background:linear-gradient(135deg,#c3b39f,#5a4c40)"></div><div class="share"><span style="background:#3b5b9a">Share</span><span style="background:#29a9e1">Post</span></div></div></article>
  <article class="post flip"><div class="post-photo photo" role="img" aria-label="Story photo" style="background:linear-gradient(135deg,#c0ccb4,#4f5f44)"><div class="post-cap"><h3>Hilarious Commentary</h3><p>Short teaser text sitting under the headline</p><a class="btn-read">Read More</a></div></div><div class="post-side"><div class="photo" role="img" aria-label="Related photo" style="background:linear-gradient(135deg,#e6d0bd,#8e6c58)"></div><div class="share"><span style="background:#3b5b9a">Share</span><span style="background:#29a9e1">Post</span></div></div></article>
  <article class="post"><div class="post-photo photo" role="img" aria-label="Group photo" style="background:linear-gradient(135deg,#b7a899,#3f352e)"><div class="post-cap"><h3>Interesting Group</h3><p>Short teaser text sitting under the headline</p><a class="btn-read">Read More</a></div></div><div class="post-side"><div class="photo" role="img" aria-label="Related photo" style="background:linear-gradient(135deg,#d0bba7,#6e5848)"></div><div class="share"><span style="background:#3b5b9a">Share</span><span style="background:#29a9e1">Post</span></div></div></article>
  <article class="post flip"><div class="post-photo photo" role="img" aria-label="Group photo" style="background:linear-gradient(135deg,#c9b6c8,#4e3d55)"><div class="post-cap"><h3>Interesting Group</h3><p>Short teaser text sitting under the headline</p><a class="btn-read">Read More</a></div></div><div class="post-side"><div class="photo" role="img" aria-label="Related photo" style="background:linear-gradient(135deg,#dcc6b0,#7a5c48)"></div><div class="share"><span style="background:#3b5b9a">Share</span><span style="background:#29a9e1">Post</span></div></div></article>
  <article class="post"><div class="post-photo photo" role="img" aria-label="Story photo" style="background:linear-gradient(135deg,#d4b8a0,#5b3f30)"><div class="post-cap"><h3>Outrageous Info</h3><p>Short teaser text sitting under the headline</p><a class="btn-read">Read More</a></div></div><div class="post-side"><div class="photo" role="img" aria-label="Related photo" style="background:linear-gradient(135deg,#bfc9d4,#4b586a)"></div><div class="share"><span style="background:#3b5b9a">Share</span><span style="background:#29a9e1">Post</span></div></div></article>
  <article class="post flip"><div class="post-photo photo" role="img" aria-label="Story photo" style="background:linear-gradient(135deg,#e0c4ac,#7c573f)"><div class="post-cap"><h3>Hilarious Commentary</h3><p>Short teaser text sitting under the headline</p><a class="btn-read">Read More</a></div></div><div class="post-side"><div class="photo" role="img" aria-label="Related photo" style="background:linear-gradient(135deg,#cbb6a3,#5e4a3c)"></div><div class="share"><span style="background:#3b5b9a">Share</span><span style="background:#29a9e1">Post</span></div></div></article>
  <article class="post"><div class="post-photo photo" role="img" aria-label="Story photo" style="background:linear-gradient(135deg,#c6b29e,#4a3b30)"><div class="post-cap"><h3>Outrageous Info</h3><p>Short teaser text sitting under the headline</p><a class="btn-read">Read More</a></div></div><div class="post-side"><div class="photo" role="img" aria-label="Related photo" style="background:linear-gradient(135deg,#dfcab6,#86685a)"></div><div class="share"><span style="background:#3b5b9a">Share</span><span style="background:#29a9e1">Post</span></div></div></article>
</main>

<aside class="side abs">
  <div class="weather"><div class="photo" role="img" aria-label="Weather scene" style="background:linear-gradient(135deg,#6fa6d8,#2a4f80)"></div><div><h5>Today in Sydney</h5><div class="temp">21°</div><p>Sunny with light winds</p></div></div>
  <div class="ad-mrec photo" role="img" aria-label="Harbrook 71 shopping centre advertisement"><span>Harbrook 71</span></div>
  <div class="video">
    <h5>Pelinora has a cuppa and a chat with Tessa Arlow</h5>
    <div class="photo" role="img" aria-label="Video still of the interview" style="background:linear-gradient(135deg,#a9b7c8,#34445a)">
      <svg class="play" viewBox="0 0 44 44"><circle cx="22" cy="22" r="21" fill="rgba(0,0,0,.55)"/><path d="M17 13 L32 22 L17 31Z" fill="#fff"/></svg>
    </div>
    <div class="btns"><a class="btn" style="background:var(--blue)">View Full Post</a><a class="btn" style="background:var(--red)">More Videos</a></div>
  </div>
  <div class="signup">
    <h5>Sign Up For Pelinora Daily sent to your inbox</h5>
    <div class="row"><span class="field">Enter Your Email</span><a class="btn" style="background:var(--blue)">Get More</a></div>
    <div class="follow">FOLLOW US <i class="dot" style="background:#3b5b9a"></i><i class="dot" style="background:#29a9e1"></i><i class="dot" style="background:#d9342b"></i><i class="dot" style="background:#f08a24"></i></div>
  </div>
  <div class="fb">
    <div class="fb-head">Find us on Circlebook</div>
    <div class="fb-page"><div class="photo" role="img" aria-label="Page avatar" style="background:var(--pink)"></div><div><b>Pelinora</b><p>48,210 people like Pelinora.</p></div></div>
    <div class="fb-grid">
      <div role="img" aria-label="Follower avatar"></div><div role="img" aria-label="Follower avatar"></div><div role="img" aria-label="Follower avatar"></div><div role="img" aria-label="Follower avatar"></div><div role="img" aria-label="Follower avatar"></div><div role="img" aria-label="Follower avatar"></div>
      <div role="img" aria-label="Follower avatar"></div><div role="img" aria-label="Follower avatar"></div><div role="img" aria-label="Follower avatar"></div><div role="img" aria-label="Follower avatar"></div><div role="img" aria-label="Follower avatar"></div><div role="img" aria-label="Follower avatar"></div>
      <div role="img" aria-label="Follower avatar"></div><div role="img" aria-label="Follower avatar"></div><div role="img" aria-label="Follower avatar"></div><div role="img" aria-label="Follower avatar"></div><div role="img" aria-label="Follower avatar"></div><div role="img" aria-label="Follower avatar"></div>
    </div>
    <div class="fb-foot">Circlebook social plugin</div>
  </div>
  <div class="galleries">
    <h5>Photo Galleries</h5>
    <div class="gal-grid">
      <div><div class="photo" role="img" aria-label="Gallery cover" style="background:linear-gradient(135deg,#d8c2ae,#7a5e4c)"></div><p>Red carpet looks of the week</p></div>
      <div><div class="photo" role="img" aria-label="Gallery cover" style="background:linear-gradient(135deg,#c0cfdd,#4b5f78)"></div><p>Best dressed at the awards</p></div>
      <div><div class="photo" role="img" aria-label="Gallery cover" style="background:linear-gradient(135deg,#e3c6b2,#8a5f4a)"></div><p>Summer style for less</p></div>
      <div><div class="photo" role="img" aria-label="Gallery cover" style="background:linear-gradient(135deg,#cdbfd6,#5c4a6a)"></div><p>Wedding dresses we love</p></div>
      <div><div class="photo" role="img" aria-label="Gallery cover" style="background:linear-gradient(135deg,#d2c9b0,#6e6446)"></div><p>Celebrity kids grown up</p></div>
      <div><div class="photo" role="img" aria-label="Gallery cover" style="background:linear-gradient(135deg,#dcbcb8,#7a4e4a)"></div><p>Street style snapshots</p></div>
    </div>
  </div>
  <div class="zodiac photo" role="img" aria-label="Horoscope wheel advertisement"></div>
</aside>

<section class="band abs" style="top:1625px">
  <span class="band-tab" style="background:var(--blue)">Entertainment</span>
  <div class="band-body">
    <div class="mosaic" style="grid-template-columns:190px 120px 120px 118px;grid-template-rows:118px 118px">
      <div class="photo" role="img" aria-label="Celebrity portrait" style="grid-row:span 2;background:linear-gradient(135deg,#d6b9a2,#5e4233)"></div>
      <div class="photo" role="img" aria-label="Celebrity photo" style="background:linear-gradient(135deg,#c4ccd6,#4c5868)"></div>
      <div class="photo" role="img" aria-label="Celebrity photo" style="background:linear-gradient(135deg,#e0c8b0,#86654e)"></div>
      <div class="photo" role="img" aria-label="Celebrity photo" style="background:linear-gradient(135deg,#cdb4c4,#5c4052)"></div>
      <div class="photo" role="img" aria-label="Celebrity photo" style="grid-column:span 2;background:linear-gradient(135deg,#bfae9e,#463a30)"></div>
      <div class="photo" role="img" aria-label="Celebrity photo" style="background:linear-gradient(135deg,#d9c4b6,#74584a)"></div>
    </div>
    <div class="copy">
      <p>Lorem Ipsum is simply dummy text of the printing and typesetting industry. Lorem Ipsum has been the industry's standard dummy text ever since the 1500s, when an unknown printer took a galley.</p>
      <div class="share"><span style="background:#3b5b9a">Share</span><span style="background:#29a9e1">Post</span><span style="background:var(--red)">Comments</span></div>
      <p>Lorem Ipsum is simply dummy text of the printing and typesetting industry. Lorem Ipsum has been the industry's standard dummy text ever since the 1500s, when an unknown printer took a galley.</p>
      <div class="share"><span style="background:#3b5b9a">Share</span><span style="background:#29a9e1">Post</span><span style="background:var(--red)">Comments</span></div>
    </div>
  </div>
</section>

<section class="band abs" style="top:1915px">
  <span class="band-tab" style="background:var(--pink)">Wellbeing</span>
  <div class="band-body">
    <div class="mosaic" style="grid-template-columns:400px 156px;grid-template-rows:140px 140px">
      <div class="photo" role="img" aria-label="Woman relaxing outdoors" style="grid-row:span 2;background:linear-gradient(135deg,#d4e0c4,#6d8456)"></div>
      <div class="photo" role="img" aria-label="Healthy lifestyle photo" style="background:linear-gradient(135deg,#e6cfbb,#8c6a54)"></div>
      <div class="photo" role="img" aria-label="Healthy lifestyle photo" style="background:linear-gradient(135deg,#c6d3de,#4f6276)"></div>
    </div>
    <div class="copy">
      <p>Lorem Ipsum is simply dummy text of the printing and typesetting industry. Lorem Ipsum has been the industry's standard dummy text ever since the 1500s, when an unknown printer took a galley.</p>
      <div class="share"><span style="background:#3b5b9a">Share</span><span style="background:#29a9e1">Post</span><span style="background:var(--red)">Comments</span></div>
      <p>Lorem Ipsum is simply dummy text of the printing and typesetting industry. Lorem Ipsum has been the industry's standard dummy text ever since the 1500s, when an unknown printer took a galley.</p>
      <div class="share"><span style="background:#3b5b9a">Share</span><span style="background:#29a9e1">Post</span><span style="background:var(--red)">Comments</span></div>
    </div>
  </div>
</section>

<footer class="footer abs">
  <div class="brand-name"><i></i>Pelinora</div>
  <div class="brand-tag">what everyone is talking about</div>
  <div class="foot-cols">
    <ul><li>Pelinora</li><li>About</li><li>Advertise with us</li><li>Write for us</li><li>Contact</li><li>Careers</li><li>Media kit</li><li>Newsletter</li><li>Privacy policy</li><li>Site map</li></ul>
    <ul><li>Dating</li><li>Sex</li><li>Weddings</li><li>Break ups</li><li>Friendship</li><li>Family</li><li>Work</li><li>Money</li><li>Health</li></ul>
    <ul><li>Motherhood</li><li>Pregnancy</li><li>Babies</li><li>Toddlers</li><li>Teens</li><li>Schooling</li><li>Body image</li><li>Food and recipes</li><li>Fitness</li></ul>
    <ul><li>Celebs and gossip</li><li>Movies</li><li>Television</li><li>Music</li><li>Books</li><li>Fashion</li><li>Beauty</li><li>Travel</li></ul>
    <div class="stay"><h6>STAY CONNECTED</h6><i class="dot" style="background:#3b5b9a"></i> <i class="dot" style="background:#29a9e1"></i> <i class="dot" style="background:#d9342b"></i> <i class="dot" style="background:#f08a24"></i></div>
  </div>
  <div class="legal">© Copyright 2012 Pelinora · Terms of Service</div>
  <div class="badge"></div>
</footer>

</body>
</html>
```